Business Card Design Project

Looking for a logo and business card for a Real State Business i will be opening. The name is not choosen yet , but will probably be RWT IMOVEIS.
I was thinking black and silver colors, but am open to nice ideas.
I did add a business card that i liked a lot, am looking for something like that, with logo in black or silver in a black card. The logo i was thinking in the letters RWT as i uploaded or something or little and cute buildings or a house...just ideas, can be any nice logo.
Updates

You guys can add other colors if you want, I like colors very "BRIGHT" and "open", like red, pink, strong colors. almost glow in the dark colors. lol

Designers,

I've increased more 88 dollars in the budget for 1st place cause I will want envelope designs... small and big sizes.

So 1st place is now U$248,00. 

No need to send the envelope designs right now... only the business cards designs.

Thank you.

Industry/Entity Type

Business

Requirements
Must have
• Marcela Tavares Rocha

www.RWTimoveis-exemplo.com.br

+554187316042

marcela@rwtimoveis-exemplo.com.br

```html
<!DOCTYPE html>
<html lang="pt-BR">
<head>
<meta charset="utf-8">
<title>RWT Imoveis – Cartão de visita</title>
<link href="https://fonts.googleapis.com/css2?family=Mulish:wght@400;700&display=swap" rel="stylesheet">
<style>
  :root{
    --bg:#e9e6e1;
    --card:#000000;
    --blue:#1a8ec4;
    --blue-deep:#0b3f5a;
    --silver:#cfcfcf;
    --grey:#9a9a9a;
    --white:#f4f4f4;
  }
  *{box-sizing:border-box;margin:0;padding:0}
  html,body{width:1200px;height:900px;overflow:hidden;background:var(--bg)}
  body{position:relative;font-family:"Mulish",sans-serif}

  .card{position:absolute;width:640px;height:360px;background:var(--card);
        box-shadow:0 10px 26px rgba(0,0,0,.35);overflow:hidden}
  .card--front{left:90px;top:60px}
  .card--back{left:470px;top:480px}

  /* front */
  .accent-band{position:absolute;left:0;top:0;width:92px;height:100%;
        background:linear-gradient(180deg,var(--blue) 0%,var(--blue-deep) 45%,#000 100%)}
  .accent-line{position:absolute;left:104px;top:0;width:3px;height:100%;
        background:linear-gradient(180deg,#555 0%,var(--silver) 40%,#fff 75%,#666 100%)}
  .brand-name{position:absolute;right:56px;top:70px;white-space:nowrap;
        color:var(--white);font-weight:400;font-size:26px;letter-spacing:1px}
  .holder{position:absolute;left:140px;top:290px;text-align:center;white-space:nowrap}
  .holder__name{color:var(--white);font-weight:700;font-size:15px}
  .holder__role{color:var(--blue);font-size:14px;margin-top:3px}
  .contacts{position:absolute;left:350px;top:262px;list-style:none;color:var(--white);
        font-size:13.5px;white-space:nowrap}
  .contacts li{display:flex;align-items:center;gap:9px;margin-bottom:12px}
  .contacts svg{flex:none}

  /* back */
  .back-name{position:absolute;left:80px;top:136px;white-space:nowrap;
        color:var(--grey);font-weight:400;font-size:24px;letter-spacing:1px}
  .website{position:absolute;right:48px;top:210px;white-space:nowrap;color:var(--white);font-size:15px}
</style>
</head>
<body>
  <section class="card card--front" aria-label="Frente do cartão">
    <div class="accent-band"></div>
    <div class="accent-line"></div>
    <p class="brand-name">RWT IMOVEIS</p>
    <div class="holder">
      <p class="holder__name">Marcela Tavares Rocha</p>
      <p class="holder__role">CEO</p>
    </div>
    <ul class="contacts">
      <li>
        <svg width="10" height="14" viewBox="0 0 10 14" aria-hidden="true"><rect x="1" y="1" width="8" height="12" rx="2" fill="none" stroke="var(--blue)" stroke-width="1.6"/><rect x="3" y="3.5" width="4" height="4" fill="var(--blue)"/></svg>
        554 187 316 042
      </li>
      <li>
        <svg width="14" height="10" viewBox="0 0 14 10" aria-hidden="true"><rect x=".8" y=".8" width="12.4" height="8.4" fill="none" stroke="var(--blue)" stroke-width="1.5"/><path d="M1 1l6 5 6-5" fill="none" stroke="var(--blue)" stroke-width="1.5"/></svg>
        marcela@rwtimoveis-exemplo.com.br
      </li>
    </ul>
  </section>

  <section class="card card--back" aria-label="Verso do cartão">
    <p class="back-name">RWT IMOVEIS</p>
    <p class="website">www.RWTimoveis-exemplo.com.br</p>
  </section>
</body>
</html>
```